Bluefinch Painting needs a Website

We need a website built for a Painting company I own, we mainly do residential painting, but don't want to be limited to that.

Need to have estimate request form.
Need pic's of past projects

I like the look of the website for http://www.harbor-brushworks.com
& "Westlake Home inspections"

My logo that was designed here on ArtHatch on the front page

I would like one of the houses I downloaded as part of the background
of the front page.

Target Market(s)

Home owners

Industry/Entity Type

Painting

Number of Pages Required

1 page

Font styles to use
Serif

Requirements
Must have
• Estimate request form for home owners to fill out -
• Name:
• Phone Number:
• Address:
• E-mail:
• Painting project description:
• And my info to:
• My phone number: (555) 318-7046
• My web address bluefinchpainting.example
Nice to have
• My logo that was designed here on ArtHatch

```html
<!DOCTYPE html>
<html lang="en">
<head>
<meta charset="utf-8">
<title>Bluefinch Painting</title>
<link href="https://fonts.googleapis.com/css2?family=Roboto+Slab:wght@300;400&family=Arimo:wght@400;700&family=Open+Sans:wght@400;600&display=swap" rel="stylesheet">
<style>
:root{
  --blue:#1a7ac4;
  --blue-dark:#1467a8;
  --ink:#1c1c1c;
  --grey-text:#555;
  --panel:#f1f1f1;
  --dark-tab:#2c2c2c;
  --line:#cfcfcf;
  --white:#fff;
}
*{box-sizing:border-box;margin:0;padding:0}
html,body{width:1137px;height:1200px;overflow:hidden;background:var(--white)}
body{position:relative;font-family:"Arimo",Arial,sans-serif;color:var(--ink)}
.abs{position:absolute}

/* header */
.brand{left:152px;top:44px;display:flex;align-items:center;gap:12px}
.brand-mark{width:40px;height:40px;background:var(--blue)}
.brand-name{font-family:"Roboto Slab",serif;font-weight:400;font-size:29px;color:var(--ink);letter-spacing:1px;line-height:1}
.call{left:836px;top:16px;display:flex;gap:8px;align-items:flex-start}
.call-label{font-size:13px;color:#333;line-height:15px}
.call-number{font-size:19px;color:#333;line-height:22px}
.nav{top:67px;left:559px;display:flex;align-items:center;font-size:12px;color:#222;text-transform:uppercase}
.nav a{color:inherit;text-decoration:none;margin-right:21px}
.nav a.active{background:var(--blue);color:var(--white);padding:6px 13px;margin-right:19px}

/* hero */
.hero{left:0;top:110px;width:1137px;height:376px;
  background:linear-gradient(180deg,#7fb2de 0%,#b9d2e8 18%,#8c8476 36%,#9a8f7a 55%,#5f7f3e 72%,#3e6a2a 88%,#c25a7a 100%)}
.hero-title{right:151px;top:183px;text-align:right;font-family:"Roboto Slab",serif;font-size:28px;line-height:36px;color:var(--white);text-shadow:1px 1px 3px rgba(0,0,0,.6);text-transform:uppercase}
.arrow{top:282px;width:32px;height:28px;background:rgba(40,40,40,.75);display:flex;align-items:center;justify-content:center}
.arrow.prev{left:6px}.arrow.next{left:1095px}
.tab{top:443px;height:43px;width:233px;font-family:"Roboto Slab",serif;font-size:17px;color:var(--white);padding:14px 0 0 12px;text-transform:uppercase}
.tab.residential{left:152px;background:var(--blue)}
.tab.commercial{left:409px;background:var(--dark-tab)}

/* gallery */
.gallery{left:152px;top:486px;width:834px;height:204px;background:linear-gradient(180deg,#ececec,#f7f7f7)}
.filter{left:171px;top:503px;font-family:"Roboto Slab",serif;font-size:18px;display:flex;align-items:center}
.filter .sep{width:1px;height:22px;background:#999;margin:0 10px}
.filter .on{color:var(--blue)}
.thumb{top:544px;width:146px;height:117px;border:1px solid #333;background:var(--white);padding:4px}
.thumb-img{width:100%;height:100%;position:relative}
.thumb-label{position:absolute;left:0;right:0;bottom:0;height:25px;background:rgba(0,0,0,.45);color:var(--white);font-family:"Roboto Slab",serif;font-size:14px;padding:3px 0 0 7px}

/* welcome */
.welcome{left:0;top:692px;width:1137px;height:209px;background:linear-gradient(135deg,#3a3d3f,#262829 45%,#3c3f41 75%,#232526)}
.welcome-title{left:0;width:1137px;top:714px;text-align:center;font-family:"Roboto Slab",serif;font-size:19px;color:var(--white)}
.welcome-rule{left:405px;top:741px}
.welcome-text{left:158px;width:820px;top:767px;text-align:center;font-size:11.6px;line-height:21px;color:var(--white)}
.read-more{left:526px;top:853px;width:84px;height:26px;border:2px solid #ddd;border-radius:4px;color:var(--white);font-size:12px;font-weight:700;text-align:center;line-height:22px}

/* quote */
.quote{left:170px;top:927px;width:796px;height:183px;border:1px solid #d4d4d4;border-radius:8px}
.quote-title{left:183px;top:932px;font-family:"Roboto Slab",serif;font-weight:300;font-size:19px;color:#444;border-bottom:2px dotted #bbb;width:245px;padding-bottom:4px}
.quote-intro{left:183px;top:975px;width:250px;font-size:12px;line-height:19px;color:#333}
.offer-label{left:183px;top:1025px;font-size:12px;color:#333;border-bottom:2px dotted #bbb;padding-bottom:3px;width:62px}
.offers{left:184px;top:1050px;list-style:none;font-size:12px;color:#333}
.offers li{display:flex;align-items:center;gap:10px;height:20px}
.divider{left:475px;top:927px}
.field{height:34px;border:1px solid #d8d8d8;font-family:"Open Sans",sans-serif;font-style:italic;font-size:12px;color:#555;padding:9px 11px;background:var(--white)}
.send{left:880px;top:1065px;width:67px;height:26px;background:var(--blue);color:var(--white);font-family:"Open Sans",sans-serif;font-weight:600;font-size:13px;text-align:center;line-height:26px;box-shadow:0 2px 0 #c9c9c9}

/* footer */
.footer{left:0;top:1136px;width:1137px;height:64px;background:var(--blue)}
.footer-nav{left:157px;top:1149px;font-size:11.5px;color:var(--white);display:flex;gap:17px}
.copyright{left:153px;top:1171px;font-size:11px;color:var(--white)}
.footer-brand{left:772px;top:1152px;display:flex;align-items:center;gap:10px}
.footer-brand .brand-mark{width:28px;height:28px;background:var(--white)}
.footer-brand .brand-name{font-size:21px;color:var(--white)}
</style>
</head>
<body>

<header>
  <div class="abs brand">
    <span class="brand-mark"></span>
    <span class="brand-name">BLUEFINCH PAINTING</span>
  </div>
  <div class="abs call">
    <svg width="28" height="28" viewBox="0 0 28 28" aria-hidden="true">
      <circle cx="14" cy="14" r="12.5" fill="none" stroke="#1a7ac4" stroke-width="1.5"/>
      <path d="M11 8c-2 1-3 3-2 6s3 6 6 7c1 0 2 0 3-1l-2-3-2 1c-1-1-2-3-2-4l2-1z" fill="#1a7ac4"/>
    </svg>
    <div>
      <div class="call-label">Call Us Today</div>
      <div class="call-number">555-318-7046</div>
    </div>
  </div>
  <nav class="abs nav">
    <a class="active" href="#">Home</a>
    <a href="#">About Us</a>
    <a href="#">Services</a>
    <a href="#">Past Projects</a>
    <a href="#" style="margin-right:0">Contact Us</a>
  </nav>
</header>

<section>
  <div class="abs hero" role="img" aria-label="Two-storey craftsman house with grey siding, stone accents and flowering garden in front"></div>
  <h1 class="abs hero-title">Providing quality work at<br>affordable prices</h1>
  <div class="abs arrow prev"><svg width="10" height="12" viewBox="0 0 10 12"><path d="M7 1 2 6l5 5" fill="none" stroke="#fff" stroke-width="2.5"/></svg></div>
  <div class="abs arrow next"><svg width="10" height="12" viewBox="0 0 10 12"><path d="M3 1l5 5-5 5" fill="none" stroke="#fff" stroke-width="2.5"/></svg></div>
  <div class="abs tab residential">Residential Painting</div>
  <div class="abs tab commercial">Commercial Painting</div>
</section>

<section>
  <div class="abs gallery"></div>
  <div class="abs filter"><span>Interior</span><span class="sep"></span><span class="on">Exterior</span></div>
  <div class="abs thumb" style="left:166px"><div class="thumb-img" role="img" aria-label="Grey two-storey house with garden" style="background:linear-gradient(180deg,#5f95cf,#8a8374 45%,#4d7535 80%)"><div class="thumb-label">Lorem Ispum</div></div></div>
  <div class="abs thumb" style="left:330px"><div class="thumb-img" role="img" aria-label="Painter working on white siding" style="background:linear-gradient(160deg,#2e6ec0 20%,#c8ccd2 40%,#9aa0a8)"><div class="thumb-label">Lorem Ispum</div></div></div>
  <div class="abs thumb" style="left:494px"><div class="thumb-img" role="img" aria-label="Painter spraying a yellow wall" style="background:linear-gradient(180deg,#d9cf94,#c8b877 60%,#b7a66a)"><div class="thumb-label">Lorem Ispum</div></div></div>
  <div class="abs thumb" style="left:658px"><div class="thumb-img" role="img" aria-label="Tan stucco house with green lawn" style="background:linear-gradient(180deg,#9bc1e4,#b9a993 45%,#3f8a35 80%)"><div class="thumb-label">Lorem Ispum</div></div></div>
  <div class="abs thumb" style="left:822px"><div class="thumb-img" role="img" aria-label="Grey house with large windows and porch" style="background:linear-gradient(180deg,#6b6e78,#8f8b86 50%,#4a4c50)"><div class="thumb-label">Lorem Ispum</div></div></div>
</section>

<section>
  <div class="abs welcome" role="img" aria-label="Company work truck and trailer parked in a driveway, darkened"></div>
  <h2 class="abs welcome-title" style="font-weight:400">Welcome to Bluefinch Painting</h2>
  <svg class="abs welcome-rule" width="327" height="14" viewBox="0 0 327 14" aria-hidden="true">
    <line x1="0" y1="5" x2="327" y2="5" stroke="#fff" stroke-width="1"/>
    <line x1="0" y1="8" x2="327" y2="8" stroke="#fff" stroke-width="1"/>
    <path d="M158 1l11 12M169 1l-11 12" stroke="#fff" stroke-width="1.3"/>
  </svg>
  <p class="abs welcome-text">Lorem ipsum dolor sit amet, consectetuer adipiscing elit, sed diam nonummy nibh euismod&nbsp; consequat. Duis autem revel eum iriure dolor in hendrerit in vulputate velit esse molestie consequat.Lorem ipsum dolor sit amet, consectetuer adipiscing elit, sed diam nonummy nibh euismod&nbsp; rent ut laoreet dolore magna aliquam erat volutpat. Ut wisi enim ad minim veniam, quis nostrud lore xererci sl ut aliquip ex ea commodo consequat.</p>
  <div class="abs read-more">Read More</div>
</section>

<section>
  <div class="abs quote"></div>
  <h3 class="abs quote-title">Consultation / Quote...</h3>
  <p class="abs quote-intro">Lorem ipsum dolor sit amet, consectetuer adipiscing elit, sed diam nonummy co.</p>
  <div class="abs offer-label">We offer:</div>
  <ul class="abs offers">
    <li><svg width="11" height="11" viewBox="0 0 11 11"><circle cx="5" cy="6" r="4" fill="none" stroke="#1a7ac4" stroke-width="1.3"/><path d="M3 6l2 2 5-7" fill="none" stroke="#1a7ac4" stroke-width="1.5"/></svg>Lorem ipsum dolor sit amet, consectetuer</li>
    <li><svg width="11" height="11" viewBox="0 0 11 11"><circle cx="5" cy="6" r="4" fill="none" stroke="#1a7ac4" stroke-width="1.3"/><path d="M3 6l2 2 5-7" fill="none" stroke="#1a7ac4" stroke-width="1.5"/></svg>Lorem ipsum dolor sit amet, consectetuer</li>
  </ul>
  <svg class="abs divider" width="11" height="184" viewBox="0 0 11 184" aria-hidden="true">
    <g fill="none" stroke="#d0d0d0" stroke-width="1">
      <circle cx="5.5" cy="4" r="3.5"/><circle cx="5.5" cy="17" r="3.5"/><circle cx="5.5" cy="30" r="3.5"/><circle cx="5.5" cy="43" r="3.5"/><circle cx="5.5" cy="56" r="3.5"/><circle cx="5.5" cy="69" r="3.5"/><circle cx="5.5" cy="82" r="3.5"/><circle cx="5.5" cy="95" r="3.5"/><circle cx="5.5" cy="108" r="3.5"/><circle cx="5.5" cy="121" r="3.5"/><circle cx="5.5" cy="134" r="3.5"/><circle cx="5.5" cy="147" r="3.5"/><circle cx="5.5" cy="160" r="3.5"/><circle cx="5.5" cy="173" r="3.5"/>
    </g>
  </svg>
  <div class="abs field" style="left:519px;top:940px;width:206px">First Name</div>
  <div class="abs field" style="left:742px;top:938px;width:205px">Phone</div>
  <div class="abs field" style="left:519px;top:979px;width:206px">Email</div>
  <div class="abs field" style="left:742px;top:978px;width:205px">Phone Number</div>
  <div class="abs field" style="left:519px;top:1018px;width:348px;height:74px">Details of inquiry</div>
  <div class="abs send">Send</div>
</section>

<footer>
  <div class="abs footer"></div>
  <div class="abs footer-nav"><span>• Home</span><span>• About Us</span><span>• Services</span><span>• Past Projects</span><span>• Contact Us</span></div>
  <div class="abs copyright">Copyright ©2015, BluefinchPainting&nbsp; All Rights Reserved</div>
  <div class="abs footer-brand">
    <span class="brand-mark"></span>
    <span class="brand-name">BLUEFINCH PAINTING</span>
  </div>
</footer>

</body>
</html>
```